Business Card Design

Just looking for a good designs that looks good with our company logo. I'd like it to be simple and to the point. Just including contact information, our logo, and my name somewhere on the card so future clients know who they're contacting, and a couple services offered. The two images I attached are pictures of our logo. I don't care which color they they are, I just attached both images to give a reference of logo colors depending on the color of the card.
Names: Carl Whitby
Phone: 816-555-0147
Email: greenstripeyard@fernmail.test
Services offered:
Mowing
Fertilization
Aeration
Bed & tree maintenance
and more.
Business
Names: Carl Whitby
Phone: 816-555-0147
(no website)

```html
<!DOCTYPE html>
<html lang="en">
<head>
<meta charset="utf-8">
<title>Fairway Turf – Business Card</title>
<link href="https://fonts.googleapis.com/css2?family=Open+Sans:wght@400;600;700&display=swap" rel="stylesheet">
<style>
  :root {
    --backdrop: #2b2b2d;
    --card: #fbfbfb;
    --ink: #3a3b45;
    --navy: #3b3f56;
    --orange: #f0533a;
  }
  html, body {
    margin: 0;
    width: 1200px;
    height: 943px;
    overflow: hidden;
    background: var(--backdrop);
    font-family: "Open Sans", Arial, sans-serif;
  }
  .card {
    position: absolute;
    left: 100px;
    top: 186px;
    width: 1000px;
    height: 572px;
    background: var(--card);
    border-radius: 4px;
    overflow: hidden;
    box-shadow: 0 12px 30px rgba(0,0,0,.45);
  }
  .brand {
    position: absolute;
    left: 70px;
    top: 96px;
    display: flex;
    align-items: center;
    gap: 18px;
    white-space: nowrap;
  }
  .brand-dot {
    width: 48px;
    height: 48px;
    border-radius: 50%;
    background: var(--orange);
    flex: none;
  }
  .brand-name {
    font-size: 42px;
    font-weight: 700;
    color: var(--navy);
    letter-spacing: 1px;
    text-transform: uppercase;
  }
  .holder {
    position: absolute;
    right: 70px;
    top: 72px;
    margin: 0;
    font-size: 52px;
    font-weight: 600;
    color: var(--ink);
    white-space: nowrap;
  }
  .services {
    position: absolute;
    left: 580px;
    top: 170px;
    margin: 0;
    padding: 0;
    list-style: none;
    font-size: 29px;
    line-height: 1.42;
    color: var(--ink);
    white-space: nowrap;
  }
  .services li::before { content: "-"; }
  .contact {
    position: absolute;
    left: 60px;
    right: 60px;
    bottom: 86px;
    display: flex;
    gap: 30px;
  }
  .pill {
    display: flex;
    align-items: center;
    gap: 16px;
    height: 72px;
    padding: 0 24px 0 14px;
    border-radius: 14px;
    background: var(--orange);
    color: var(--ink);
    white-space: nowrap;
    box-sizing: border-box;
  }
  .pill-icon {
    width: 50px;
    height: 50px;
    flex: none;
  }
  .pill-email { flex: none; font-size: 22px; }
  .pill-phone { flex: 1; font-size: 36px; letter-spacing: 1px; }
  .edge-orange {
    position: absolute;
    left: 0; right: 0;
    bottom: 26px;
    height: 26px;
    background: var(--orange);
  }
  .edge-navy {
    position: absolute;
    left: 0; right: 0;
    bottom: 0;
    height: 26px;
    background: var(--navy);
  }
</style>
</head>
<body>
  <section class="card">
    <div class="brand">
      <span class="brand-dot"></span>
      <span class="brand-name">Fairway Turf</span>
    </div>

    <h1 class="holder">Carl Whitby</h1>
    <ul class="services">
      <li>Mowing</li>
      <li>Fertilization</li>
      <li>Aeration</li>
      <li>Bed &amp; tree maintenance</li>
    </ul>

    <div class="contact">
      <div class="pill pill-email">
        <svg class="pill-icon" viewBox="0 0 50 50" aria-hidden="true">
          <circle cx="25" cy="25" r="23" fill="none" stroke="#3a3b45" stroke-width="3"/>
          <rect x="13" y="16" width="24" height="18" rx="1" fill="none" stroke="#3a3b45" stroke-width="2.5"/>
          <path d="M13 17 L25 27 L37 17" fill="none" stroke="#3a3b45" stroke-width="2.5"/>
        </svg>
        <span>greenstripeyard@fernmail.test</span>
      </div>
      <div class="pill pill-phone">
        <svg class="pill-icon" viewBox="0 0 50 50" aria-hidden="true">
          <circle cx="25" cy="25" r="23" fill="none" stroke="#3a3b45" stroke-width="3"/>
          <rect x="17" y="11" width="16" height="28" rx="3" fill="none" stroke="#3a3b45" stroke-width="2.5"/>
          <line x1="21" y1="34" x2="29" y2="34" stroke="#3a3b45" stroke-width="2.5"/>
        </svg>
        <span>816-555-0147</span>
      </div>
    </div>

    <div class="edge-orange"></div>
    <div class="edge-navy"></div>
  </section>
</body>
</html>
```